Local Flower Farm Needs Business Card Design

I need business cards designed for a flower farm based in Eudora, Kansas.
Business Info:
We are a local cut flower farm located in Eudora, Kansas, founded by Corinne Haldwick. What started as a passion for agriculture and search for more joy in daily life has blossomed into a small business dedicated to providing the community with beautiful, fresh, and sustainable flowers. We specialize in local, seasonal blooms, ensuring that every petal reflects the care and dedication we pour into our craft. Our mission is to deliver the highest quality flowers directly to our customers through local farmers markets and to florists who share our commitment to sustainability. Join us in celebrating the beauty of nature, one bloom at a time!
Contact Details:
Corinne Haldwick
Owner
Phone 913-555-0147
Facebook: Rosalind Thorpe Gardens
Instagram: @RosalindThorpeGardens
Website: RosalindThorpeGardens.example
Target Market(s)
Wholesale to Florists and Direct to Consumer via Farmers Market
Industry/Entity Type
Florist, Farm
Contact Information for Business Card
Name, Contact Info, Logo
Look and feel
Each slider illustrates characteristics of the customer's brand and the style your logo design should communicate.

```html
<!DOCTYPE html>
<html lang="en">
<head>
<meta charset="utf-8">
<title>Rosalind Thorpe Gardens — Business Card</title>
<link href="https://fonts.googleapis.com/css2?family=Arimo:wght@400;700&display=swap" rel="stylesheet">
<style>
  :root {
    --backdrop: #e2e3e4;
    --paper: #f7f7f6;
    --ink: #111a1a;
    --ink-soft: #4a4f50;
    --rule: #5c6162;
    --faint: #ebecec;
  }
  * { box-sizing: border-box; margin: 0; padding: 0; }
  html, body { width: 1200px; height: 829px; overflow: hidden; }
  body {
    background: var(--backdrop);
    font-family: "Arimo", Arial, sans-serif;
    color: var(--ink);
    position: relative;
  }
  .card {
    position: absolute;
    top: 262px;
    width: 530px;
    height: 303px;
    background: var(--paper);
    box-shadow: 0 2px 6px rgba(0,0,0,0.08);
    overflow: hidden;
  }
  .card--front { left: 50px; }
  .card--back { left: 620px; }

  .front__band {
    position: absolute; left: 0; right: 0; bottom: 0;
    height: 26px; background: var(--ink);
  }
  .brand-seal {
    position: absolute;
    display: flex; align-items: center; justify-content: center;
    border: 1.5px solid var(--ink);
    border-radius: 50%;
    text-align: center;
    color: var(--ink);
    font-weight: 700;
    text-transform: uppercase;
    letter-spacing: 0.06em;
    line-height: 1.3;
  }
  .card--front .brand-seal {
    left: 50px; top: 62px; width: 150px; height: 150px; font-size: 13px;
  }
  .front__divider {
    position: absolute; left: 250px; top: 56px;
    width: 1px; height: 180px; background: var(--rule);
  }
  .contact {
    position: absolute; left: 275px; top: 62px;
  }
  .contact__name {
    font-size: 22px; font-weight: 700; text-transform: uppercase; letter-spacing: 0.01em;
  }
  .contact__role {
    font-size: 13px; color: var(--ink-soft); margin-top: 2px;
  }
  .contact__list { list-style: none; margin-top: 16px; }
  .contact__item {
    display: flex; align-items: center; gap: 7px;
    font-size: 14px; color: var(--ink-soft); margin-bottom: 6px;
  }
  .contact__icon { width: 11px; height: 11px; flex: none; }

  .back__flora {
    position: absolute; left: 60px; top: 0; width: 190px; height: 303px;
    background: linear-gradient(160deg, var(--faint), rgba(235,236,236,0.2));
  }
  .card--back .brand-seal {
    left: 255px; top: 52px; width: 200px; height: 200px; font-size: 17px;
  }
</style>
</head>
<body>
  <section class="card card--front">
    <div class="brand-seal">Rosalind<br>Thorpe<br>Gardens</div>
    <div class="front__divider"></div>
    <div class="contact">
      <h1 class="contact__name">Corinne Haldwick</h1>
      <p class="contact__role">Owner</p>
      <ul class="contact__list">
        <li class="contact__item">
          <svg class="contact__icon" viewBox="0 0 24 24"><path fill="#111a1a" d="M6.6 10.8a15.1 15.1 0 0 0 6.6 6.6l2.2-2.2a1 1 0 0 1 1-.25 11.4 11.4 0 0 0 3.6.57 1 1 0 0 1 1 1V20a1 1 0 0 1-1 1A17 17 0 0 1 3 4a1 1 0 0 1 1-1h3.5a1 1 0 0 1 1 1c0 1.25.2 2.45.57 3.57a1 1 0 0 1-.25 1z"/></svg>
          913-555-0147
        </li>
        <li class="contact__item">
          <svg class="contact__icon" viewBox="0 0 12 12"><circle cx="6" cy="6" r="5" fill="#111a1a"/></svg>
          Rosalind Thorpe Gardens
        </li>
        <li class="contact__item">
          <svg class="contact__icon" viewBox="0 0 12 12"><circle cx="6" cy="6" r="5" fill="none" stroke="#111a1a" stroke-width="1.4"/></svg>
          @RosalindThorpeGardens
        </li>
        <li class="contact__item">
          <svg class="contact__icon" viewBox="0 0 24 24"><circle cx="12" cy="12" r="10" fill="none" stroke="#111a1a" stroke-width="2"/><path d="M2 12h20M12 2c3 3 3 17 0 20M12 2c-3 3-3 17 0 20" fill="none" stroke="#111a1a" stroke-width="1.6"/></svg>
          RosalindThorpeGardens.example
        </li>
      </ul>
    </div>
    <div class="front__band"></div>
  </section>

  <section class="card card--back">
    <div class="back__flora" role="img" aria-label="Faint floral line illustration in the background"></div>
    <div class="brand-seal">Rosalind<br>Thorpe<br>Gardens</div>
  </section>
</body>
</html>
```